Website offering services oriented to the metaverse and blockchain

We need an ecommerce website theme/template for a new company named Vimbral (a play on words for KORVAND the inventor of Quorvex). Vimbral will provide metaverse services such as:
• Vimbral Coin
• Vimbral wallet
• Vimbral Exchange
• Vimbral NFT
• Vimbral Tech
• Vimbral Pay
• Vimbral CaaS (community as a service)
• Vimbral CRM
• Vimbral Experience
• Vimbral Blockchain
• Vimbral Commerce
• Vimbral Space (as in outer space)
• Vimbral Art (sub of NFT)
• Vimbral Store

You can find our actual logo at the following link, in order to show us templates aligned with our brand:
https://files.brindlevault.net/share/folders/8kLmTzqWpXcVbNdRyHsEfGaUoJi2QtYxP?mode=view

Looking forward to heard back from you,

Designs look the same

We need a WordPress ecommerce website theme/template for a new company named Vimbral (a play on words for KORVAND the inventor of Quorvex). Vimbral will provide metaverse services such as: • Vimbral Coin • Vimbral wallet • Vimbral Exchange • Vimbral NFT • Vimbral Tech • Vimbral Pay • Vimbral CaaS (community as a service) • Vimbral CRM • Vimbral Experience • Vimbral Blockchain • Vimbral Commerce • Vimbral Space (as in outer space) • Vimbral Art (sub of NFT) • Vimbral Store You can find our actual logo at the following link, in order to show us templates aligned with our brand: https://files.brindlevault.net/share/folders/8kLmTzqWpXcVbNdRyHsEfGaUoJi2QtYxP?mode=view Looking forward to heard back from you,

Target Market(s)

Blockchain & Cryptocurrency Businesses

Industry/Entity Type

B2C, B2B Services.

Other font styles liked:
• Monserrat, Helvetica, Object Sans

Requirements
Nice to have
• Light background picture,
Should not have
• Arch designs

```html
<!DOCTYPE html>
<html lang="en">
<head>
<meta charset="utf-8">
<title>Vimbral — Metaverse &amp; Blockchain Services</title>
<link href="https://fonts.googleapis.com/css2?family=PT+Sans:wght@400;700&family=Lato:ital,wght@0,400;0,700;1,400&display=swap" rel="stylesheet">
<style>
:root{
  --green:#1fc274;
  --green-dark:#12995a;
  --navy:#0a0a2c;
  --navy-mid:#0d2238;
  --teal:#1b6f7a;
  --ink:#222;
  --body:#444;
  --soft:#f3f3f4;
  --footer:#1c1c22;
  --white:#fff;
  --star:#f5a623;
  --badge:#5a6f8c;
}
*{box-sizing:border-box;margin:0;padding:0}
html,body{width:1200px;height:4060px;overflow:hidden}
body{font-family:"Lato",Helvetica,sans-serif;color:var(--body);background:var(--white);position:relative}
.section{position:absolute;left:0;width:1200px}
h1,h2,h3,h4,.brand,.btn{font-family:"PT Sans",Helvetica,sans-serif}
.btn{display:inline-block;border-radius:24px;font-weight:700;text-transform:uppercase;font-size:16px;text-align:center}
.btn-green{background:var(--green);color:var(--white)}
.btn-white{background:var(--white);color:var(--green)}
.section-title{font-size:33px;font-weight:400;color:var(--ink);text-align:center}
.section-title b{font-weight:700}
.rule{width:46px;height:3px;background:var(--green);margin:12px auto 0}

/* hero */
.hero{top:0;height:600px;background:radial-gradient(ellipse at 50% 35%,#145a66 0%,var(--navy-mid) 40%,var(--navy) 75%)}
.hero-art{position:absolute;inset:0}
.hero .brand{position:absolute;left:90px;top:24px;font-size:32px;font-weight:700;color:var(--white)}
.nav{position:absolute;left:363px;top:40px;display:flex;gap:38px;list-style:none;font-family:"PT Sans",sans-serif;font-weight:700;font-size:13px;color:var(--white)}
.hero .login{position:absolute;left:997px;top:27px;width:146px;height:45px;line-height:45px}
.hero h1{position:absolute;top:200px;width:100%;text-align:center;font-size:66px;color:var(--white);font-weight:700}
.hero p{position:absolute;top:284px;left:170px;width:860px;text-align:center;font-size:14px;line-height:30px;color:#e6ecf2}
.hero .cta{position:absolute;left:462px;top:372px;width:276px;height:43px;line-height:43px}
.hero .down{position:absolute;left:580px;top:507px}
.hero .wave{position:absolute;left:0;bottom:0}

/* certified */
.cert{top:560px;height:310px;background:var(--soft)}
.cert .badge{position:absolute;left:190px;top:52px;width:220px;height:220px;border-radius:50%;background:var(--badge)}
.cert p{position:absolute;left:548px;top:86px;width:540px;font-size:13.5px;line-height:30px;color:#333}

/* why */
.why{top:870px;height:605px}
.why .section-title{margin-top:80px}
.cards{position:absolute;top:160px;left:152px;display:flex;gap:28px}
.card{width:280px;height:360px;background:var(--white);box-shadow:0 4px 14px rgba(0,0,0,.12);text-align:center;padding:7px}
.card .ph{height:181px;border-radius:3px}
.card h3{font-size:20px;color:var(--ink);margin-top:20px}
.card .rule{width:20px;margin-top:8px}
.card p{font-size:14.5px;line-height:30px;margin-top:10px;padding:0 12px}
.link{font-family:"PT Sans",sans-serif;font-weight:700;font-size:13px;text-decoration:underline;text-transform:uppercase}
.card .link{color:var(--green);display:block;margin-top:12px}

/* who */
.who{top:1475px;height:500px;background:var(--green)}
.who .ph{position:absolute;left:0;top:0;width:600px;height:500px;background:linear-gradient(135deg,#d9d2b8 0%,#8a8468 40%,#2c3a2c 80%,#1c261e 100%)}
.who h2{position:absolute;left:652px;top:80px;font-size:33px;font-weight:400;color:var(--white)}
.who h2 b{font-weight:700}
.who .rule{position:absolute;left:652px;top:130px;margin:0;background:var(--white)}
.who p{position:absolute;left:652px;top:162px;width:450px;font-size:13.5px;line-height:30px;color:#f0fff6}
.who .btn{position:absolute;left:652px;top:375px;width:147px;height:43px;line-height:43px}

/* testimonials */
.testi{top:1975px;height:612px;background:var(--soft)}
.testi .section-title{margin-top:85px}
.people{position:absolute;top:180px;left:90px;display:flex}
.person{width:255px;text-align:center}
.person .ring{width:190px;height:190px;border-radius:50%;border:2px solid var(--green);margin:0 auto;padding:8px;background:var(--white)}
.person .ring span{display:block;width:100%;height:100%;border-radius:50%;background:linear-gradient(180deg,#d8d6d3,#8c8884)}
.person h4{margin-top:22px;font-size:16px;color:var(--ink)}
.stars{color:var(--star);font-size:12px;letter-spacing:2px;margin-top:2px}
.person p{font-style:italic;font-size:13.5px;line-height:30px;margin-top:6px;padding:0 18px}

/* blog */
.blog{top:2587px;height:773px}
.blog .section-title{margin-top:80px}
.blog .intro{position:absolute;top:155px;left:125px;width:950px;text-align:center;font-size:13.5px;line-height:30px}
.posts{position:absolute;top:301px;left:107px;display:flex;gap:28px}
.post{width:310px;text-align:center}
.post .ph{height:203px;border-radius:3px}
.post h3{font-size:16px;color:var(--ink);margin-top:22px}
.post p{font-size:14.5px;line-height:30px;margin-top:8px;padding:0 28px}
.post .link{color:var(--ink);display:block;margin-top:8px}
.arrow{position:absolute;top:388px}

/* cta */
.cta-band{top:3360px;height:340px;background:linear-gradient(180deg,#1fc274,#14a860)}
.cta-band h2{position:absolute;top:88px;width:100%;text-align:center;color:var(--white);font-size:35px;line-height:54px;font-weight:700;text-transform:uppercase}
.cta-band .btn{position:absolute;left:462px;top:212px;width:276px;height:43px;line-height:43px}
.cta-band svg{position:absolute;left:0;bottom:0}

/* footer */
.footer{top:3700px;height:360px;background:var(--footer);color:#ddd}
.footer .brand{position:absolute;left:102px;top:52px;font-size:38px;font-weight:700;color:var(--white)}
.footer .about{position:absolute;left:102px;top:125px;width:280px;font-size:13.5px;line-height:30px}
.social{position:absolute;left:102px;top:198px;display:flex;gap:11px}
.social span{width:32px;height:32px;border-radius:50%;background:var(--white);display:block;position:relative}
.social span::after{content:"";position:absolute;left:11px;top:11px;width:10px;height:10px;border-radius:50%;background:var(--green)}
.col{position:absolute;top:65px}
.col h4{font-size:15px;color:var(--white);text-transform:uppercase;margin-bottom:10px}
.col li{list-style:none;font-size:14px;line-height:30px}
.col p{font-size:13.5px;line-height:30px;width:290px}
.news{margin-top:14px;width:286px;height:44px;background:var(--white);display:flex;align-items:center;justify-content:space-between;padding:0 12px;font-size:11px;color:#666}
.copy{position:absolute;top:318px;width:100%;text-align:center;font-size:12px;color:#ccc}
.copy em{font-style:normal;color:var(--green)}
</style>
</head>
<body>

<header class="section hero">
  <div class="hero-art" role="img" aria-label="Glowing teal network of linked chain shapes on a dark navy background"></div>
  <div class="brand">VIMBRAL</div>
  <ul class="nav"><li>HOME</li><li>SERVICES</li><li>ABOUT US</li><li>TESTIMONIALS</li><li>BLOG</li><li>CONTACT US</li></ul>
  <a class="btn btn-green login">Login</a>
  <h1>WELCOME TO VIMBRAL</h1>
  <p>Lorem ipsum dolor sit amet, consectetur adipiscing elit, sed do eiusmod tempor incididunt ut labore et dolore magna aliqua. Quis ipsum suspendisse ultrices gravida. Risus commodo viverra maecenas accumsan lacus vel facilisis.</p>
  <a class="btn btn-green cta">Schedule Free Consultation</a>
  <svg class="down" width="40" height="40" viewBox="0 0 40 40"><circle cx="20" cy="20" r="18" fill="none" stroke="#fff" stroke-width="2"/><path d="M13 17l7 7 7-7" fill="none" stroke="#fff" stroke-width="2"/></svg>
  <svg class="wave" width="1200" height="80" viewBox="0 0 1200 80"><path d="M0 40 C300 70 700 80 1200 0 L1200 80 L0 80Z" fill="#6b6788"/><path d="M0 40 C350 78 800 84 1200 45 L1200 80 L0 80Z" fill="#f3f3f4"/></svg>
</header>

<section class="section cert">
  <div class="badge" role="img" aria-label="Certification badge"></div>
  <p>Lorem ipsum dolor sit amet, consectetur adipiscing elit, sed do eiusmod tempor incididunt ut labore et dolore magna aliqua. Ut enim ad minim veniam, quis nostrud exercitation ullamco laboris nisi ut aliquip ex ea commodo consequat. Duis aute irure dolor in reprehenderit in voluptate velit esse cillum dolore eu fugiat nulla pariatur. Excepteur sint occaecat cupidatat non proident, sunt in culpa qui officia deserunt mollit anim id est laborum</p>
</section>

<section class="section why">
  <h2 class="section-title">Why choose <b>Vimbral</b></h2>
  <div class="rule"></div>
  <div class="cards">
    <article class="card"><div class="ph" role="img" aria-label="Business people reviewing charts at a whiteboard" style="background:linear-gradient(135deg,#5b6c8c,#c8ced8)"></div><h3>LOREM IPSUM DOLOR</h3><div class="rule"></div><p>Lorem ipsum dolor sit amet, consectetur adipiscing elit.</p><a class="link">Learn More</a></article>
    <article class="card"><div class="ph" role="img" aria-label="Trader watching market charts on several monitors" style="background:linear-gradient(135deg,#2a2e36,#8a9cb4)"></div><h3>LOREM IPSUM DOLOR</h3><div class="rule"></div><p>Lorem ipsum dolor sit amet, consectetur adipiscing elit.</p><a class="link">Learn More</a></article>
    <article class="card"><div class="ph" role="img" aria-label="Hand writing beside a glowing digital diagram" style="background:linear-gradient(135deg,#9ab4c8,#e4ecf2)"></div><h3>LOREM IPSUM DOLOR</h3><div class="rule"></div><p>Lorem ipsum dolor sit amet, consectetur adipiscing elit.</p><a class="link">Learn More</a></article>
  </div>
</section>

<section class="section who">
  <div class="ph" role="img" aria-label="Hand holding a pen among floating digital numbers"></div>
  <h2>Who <b>we are</b></h2>
  <div class="rule"></div>
  <p>Lorem ipsum dolor sit amet, consectetur adipiscing elit, sed do eiusmod tempor incididunt ut labore et dolore magna aliqua. Quis ipsum suspendisse ultrices gravida. Risus commodo viverra maecenas accumsan lacus vel facilisis. Lorem ipsum dolor sit amet, consectetur adipiscing elit, sed do eiusmod tempor incididunt ut labore et dolore magna aliqua.</p>
  <a class="btn btn-white">Learn More</a>
</section>

<section class="section testi">
  <h2 class="section-title">Our Client <b>Testimonials</b></h2>
  <div class="rule"></div>
  <div class="people">
    <div class="person"><div class="ring"><span role="img" aria-label="Client portrait"></span></div><h4>JOHN DOE</h4><div class="stars">★★★★★</div><p>Lorem ipsum dolor sit amet, consectetur adipiscing elit, sed do eiusmod tempor</p></div>
    <div class="person"><div class="ring"><span role="img" aria-label="Client portrait"></span></div><h4>JOHN DOE</h4><div class="stars">★★★★★</div><p>Lorem ipsum dolor sit amet, consectetur adipiscing elit, sed do eiusmod tempor</p></div>
    <div class="person"><div class="ring"><span role="img" aria-label="Client portrait"></span></div><h4>JOHN DOE</h4><div class="stars">★★★★★</div><p>Lorem ipsum dolor sit amet, consectetur adipiscing elit, sed do eiusmod tempor</p></div>
    <div class="person"><div class="ring"><span role="img" aria-label="Client portrait"></span></div><h4>JOHN DOE</h4><div class="stars">★★★★★</div><p>Lorem ipsum dolor sit amet, consectetur adipiscing elit, sed do eiusmod tempor</p></div>
  </div>
</section>

<section class="section blog">
  <h2 class="section-title">Our <b>Latest Blog</b></h2>
  <div class="rule"></div>
  <p class="intro">Chainforge Studio provides a complete service that handles the development, IT operations and support for your cryptocurrency. Cryptocurrency development can be difficult and complex, and a quality development team is hard to find and expensive. Chainforge Studio has an experienced team that has helped several clients launch and enhance their cryptocurrencies, including successfully running the Lumeth cryptocurrency since 2017, and writing a next-generation cryptocurrency from scratch.</p>
  <svg class="arrow" style="left:52px" width="24" height="40" viewBox="0 0 24 40"><path d="M20 2L4 20l16 18" fill="none" stroke="#333" stroke-width="2.5"/></svg>
  <svg class="arrow" style="left:1124px;top:394px" width="24" height="40" viewBox="0 0 24 40"><path d="M4 2l16 18L4 38" fill="none" stroke="#333" stroke-width="2.5"/></svg>
  <div class="posts">
    <article class="post"><div class="ph" role="img" aria-label="Visitors in a gallery viewing a digital art display" style="background:linear-gradient(180deg,#3a2540,#7a4a6a 60%,#2a1a2c)"></div><h3>LOREM IPSUM DOLOR SIT AMET</h3><p>Lorem ipsum dolor sit amet, consectetur adipiscing elit, sed do eiusmod tempor incididunt ut labore.</p><a class="link">Learn More</a></article>
    <article class="post"><div class="ph" role="img" aria-label="Hands typing on a laptop under glowing network nodes" style="background:linear-gradient(135deg,#0f1a2c,#1f4f8a 70%,#26262e)"></div><h3>LOREM IPSUM DOLOR SIT AMET</h3><p>Lorem ipsum dolor sit amet, consectetur adipiscing elit, sed do eiusmod tempor incididunt ut labore.</p><a class="link">Learn More</a></article>
    <article class="post"><div class="ph" role="img" aria-label="Person standing before a wall of digital data screens" style="background:linear-gradient(135deg,#152238,#2c5a7a 60%,#101a2a)"></div><h3>LOREM IPSUM DOLOR SIT AMET</h3><p>Lorem ipsum dolor sit amet, consectetur adipiscing elit, sed do eiusmod tempor incididunt ut labore.</p><a class="link">Learn More</a></article>
  </div>
</section>

<section class="section cta-band">
  <h2>Lorem ipsum dolor sit amet, consectetur adipi<br>sed do eiusmod tempor incididunt ut la.</h2>
  <a class="btn btn-white">Schedule Free Consultation</a>
  <svg width="1200" height="70" viewBox="0 0 1200 70"><path d="M0 50 C300 20 700 60 1200 10 L1200 70 L0 70Z" fill="#0f5e3c"/><path d="M0 62 C350 40 800 72 1200 30 L1200 70 L0 70Z" fill="#1c1c22"/></svg>
</section>

<footer class="section footer">
  <div class="brand">VIMBRAL</div>
  <p class="about">Lorem ipsum dolor sit amet, consectetur adipiscing elit, sed do eiusmod .</p>
  <div class="social" aria-label="Social links"><span></span><span></span><span></span><span></span></div>
  <div class="col" style="left:418px"><h4>What we do</h4><ul><li>Lorem ipsum dolor sit</li><li>Amet consectetur adi</li><li>Piscing elit, sed do</li><li>Eiusmod tempor</li><li>Ncididunt ut labore</li></ul></div>
  <div class="col" style="left:613px"><h4>Quick Menu</h4><ul><li>Home</li><li>Services</li><li>About Us</li><li>Testimonials</li><li>Blog</li><li>Contact Us</li></ul></div>
  <div class="col" style="left:811px"><h4>Newsletter</h4><p>Lorem ipsum dolor sit amet, consec tetur adipiscing elit sed do.</p>
    <div class="news"><span>Enter The Email</span><svg width="16" height="16" viewBox="0 0 16 16"><path d="M1 8L15 1 11 15 8 9Z" fill="#1fc274"/></svg></div></div>
  <p class="copy">© Copyright 2021 <em>Vimbral</em>. All Rights Reserved</p>
</footer>

</body>
</html>
```